Roll up corner and Three fold flyer

I need a roll up corner and a three-fold flyer that follow the same design:

I would like to advertise Hospitality, Tourism and Culinary internships in China, Spain, and Australia.

I am attaching some samples:

1.- A roll up corner sample
2.- 4 picuters of a Three-Fold flyer of a company who also does internships in Hospitality. And I really like its flyers.
3.- Three PDF files (Australia, Spain and China) with basic information I would like in the three fold or/and the roll up corner.

Three fold size: A normal letter format
Roll up corner: 85cm x 200 cm

Target Market(s)

Students

Industry/Entity Type

Tourism

Requirements
Must have
• Company name: Northwind Ventures

```html
<!DOCTYPE html>
<html lang="es">
<head>
<meta charset="utf-8">
<title>Northwind Ventures – Trifold interior</title>
<link rel="stylesheet" href="https://fonts.googleapis.com/css2?family=Lato:wght@300;400&family=Open+Sans:wght@400&family=Josefin+Sans:wght@300;400;700&family=Poiret+One&display=swap">
<style>
  :root {
    --orange: #f3a01f;
    --orange-text: #f39c1a;
    --charcoal: #2e2d2c;
    --ink: #1d1d1b;
    --grey: #5a5a5a;
    --grey-light: #8a8a8a;
    --white: #ffffff;
  }
  * { margin: 0; padding: 0; box-sizing: border-box; }
  html, body { width: 1200px; height: 911px; overflow: hidden; background: var(--white); }
  .spread { position: relative; width: 1200px; height: 911px; background: var(--white); font-family: "Lato", sans-serif; }

  /* Left panel */
  .photo { position: absolute; }
  .photo--family { left: 0; top: 69px; width: 369px; height: 244px;
    background: linear-gradient(135deg, #8a7358 0%, #c9b79a 40%, #e6dccb 60%, #6f6252 100%); }
  .brand-block { position: absolute; left: 0; top: 313px; width: 369px; height: 150px; background: var(--charcoal);
    padding: 14px 0 0 36px; }
  .brand-block p { font-family: "Open Sans", sans-serif; color: var(--orange-text); font-size: 26px; line-height: 39px; letter-spacing: 0.3px; }
  .rule-orange { position: absolute; left: 0; top: 469px; width: 369px; height: 8px; background: var(--orange); }
  .intro { position: absolute; left: 36px; top: 497px; width: 300px; color: var(--ink); font-family: "Josefin Sans", sans-serif; font-weight: 300; }
  .intro__lead { font-size: 13.5px; line-height: 18.7px; text-transform: uppercase; margin-bottom: 18px; }
  .intro__body { font-size: 13.8px; line-height: 18.7px; }

  /* Middle panel */
  .process-title { position: absolute; left: 392px; top: 68px; font-family: "Lato", sans-serif; font-weight: 300; font-size: 29px; color: var(--orange-text); letter-spacing: 0.5px; }
  .step { position: absolute; left: 383px; width: 380px; }
  .step__num { position: absolute; left: 0; top: -8px; font-family: "Lato", sans-serif; font-weight: 300; font-size: 66px; line-height: 66px; color: var(--grey-light); }
  .step__body { margin-left: 62px; }
  .step__title { font-weight: 300; font-size: 28px; line-height: 32px; color: var(--ink); }
  .step__text { font-weight: 300; font-size: 21.5px; line-height: 30.6px; color: var(--grey); }
  .step__text--dark { color: var(--ink); }
  .step--1 { top: 118px; }
  .step--2 { top: 222px; }
  .step--3 { top: 516px; }
  .step--4 { top: 604px; }

  /* Right panel */
  .photo--service { left: 771px; top: 0; width: 429px; height: 566px;
    background: linear-gradient(160deg, #c7c7b2 0%, #e9e5d8 35%, #f2efe8 55%, #b67e62 80%, #d8d2c8 100%); }
  .claim { position: absolute; left: 771px; top: 566px; width: 429px; height: 150px; background: var(--orange);
    padding: 18px 0 0 43px; color: var(--white); font-family: "Poiret One", sans-serif; font-size: 30px; line-height: 40px; letter-spacing: 0.5px; }
  .claim strong { font-family: "Josefin Sans", sans-serif; font-weight: 700; }
  .rule-charcoal { position: absolute; left: 771px; top: 722px; width: 429px; height: 9px; background: var(--charcoal); }

  /* Footer band */
  .footer-band { position: absolute; left: 368px; top: 739px; width: 832px; height: 172px; background: var(--orange); }
  .address { position: absolute; right: 486px; top: 28px; text-align: right; color: var(--white); font-family: "Poiret One", sans-serif; font-size: 18.5px; line-height: 23px; font-style: normal; }
  .tagline { position: absolute; left: 490px; top: 80px; color: var(--ink); font-family: "Josefin Sans", sans-serif; font-weight: 400; font-size: 14px; letter-spacing: 0.3px; }
</style>
</head>
<body>
<main class="spread">
  <!-- Left panel -->
  <div class="photo photo--family" role="img" aria-label="Family relaxing on beds in a hotel room, reading a newspaper"></div>
  <div class="brand-block">
    <p>NORTHWIND VENTURES</p>
    <p>IT’S NOT A HOTEL,</p>
    <p>IT’S A WAY OF LIFE</p>
  </div>
  <div class="rule-orange"></div>
  <section class="intro">
    <p class="intro__lead">Lorem ipsum dolor sit amet, consectetur adipisicing elit, sed do eiusmod tempor incididunt ut labore et dolore magna aliqua.</p>
    <p class="intro__body">Ut enim ad minim veniam, quis nostrud exercitation ullamco laboris nisi ut aliquip ex ea commodo consequat. Duis aute irure dolor in reprehenderit in voluptate velit esse cillum dolore eu fugiat nulla pariatur. Excepteur sint occaecat cupidatat non proident, sunt in culpa qui officia deserunt mollit anim id est laborum. Sed ut perspiciatis unde omnis iste natus error sit voluptatem accusantium doloremque laudantium, totam rem aperiam, eaque ipsa quae ab illo inventore veritatis et quasi architecto</p>
  </section>

  <!-- Middle panel -->
  <h2 class="process-title">OUR PROCESS</h2>
  <section class="step step--1">
    <span class="step__num">1</span>
    <div class="step__body">
      <h3 class="step__title">Puestos</h3>
      <p class="step__text">Front desk / F&amp;B / Guest<br>1 Relations</p>
    </div>
  </section>
  <section class="step step--2">
    <span class="step__num">2</span>
    <div class="step__body">
      <h3 class="step__title">Incluye</h3>
      <p class="step__text">-Colocación de trabajo<br>-Remuneración $400<br>-Alojamiento<br>-Alimentos en horarios de trabajo<br>-Asistencia en trámites de visa<br>-Guia Wanderleaf<br>-Recepción en el aeropuerto<br>-Beca de Chino Mandarin</p>
    </div>
  </section>
  <section class="step step--3">
    <span class="step__num">3</span>
    <div class="step__body">
      <h3 class="step__title">Periodo</h3>
      <p class="step__text step__text--dark">De 4 a 6 meses</p>
    </div>
  </section>
  <section class="step step--4">
    <span class="step__num">4</span>
    <div class="step__body">
      <h3 class="step__title">Inversión</h3>
      <p class="step__text">Inscripción: $290<br>Programa: $1990 a pagos</p>
    </div>
  </section>

  <!-- Right panel -->
  <div class="photo photo--service" role="img" aria-label="Waitress serving a tray of canapés at a banquet table"></div>
  <div class="claim">
    <p><strong>FIFTY</strong> HOTELS.</p>
    <p>TWENTY-TWO <strong>COUNTRIES.</strong></p>
    <p><strong>ONE</strong> PHILOSOPHY</p>
  </div>
  <div class="rule-charcoal"></div>

  <!-- Footer band -->
  <footer class="footer-band">
    <address class="address">Permanent Address<br>Dana Whitfield Marrow<br>48 Linden Court<br>Brookhaven OR<br>97301</address>
    <p class="tagline">Lorem ipsum dolor sit amet, consectetur</p>
  </footer>
</main>
</body>
</html>
```